KRT Engineering Business Card Design

We’re looking for an elegant, clean, and timeless business card design that communicates experience, capability, and reliability.

KRT Engineering was established in 1995 , we are a Government Contracting company providing Professional Services to the Office of Frontier Affairs, Harbor Protection and the Vantage Collective. Our capabilities include: Acquisition & Program Management; Intelligence & Security Operations; Cyber, IT & Network Operations; Lifecycle Logistics & Asset Readiness; C5ISR Systems Engineering & Sustainment.

We want the card to reflect a straightforward, confident approach to business. The design should feel polished and professional without being flashy or overly corporate.

Design Direction
Clean, sophisticated, and uncluttered
Elegant but understated
Strong typography and thoughtful spacing
A timeless aesthetic rather than something overly trendy
Confident and established, with a sense of substance
Easy to read and practical in a real-world business setting

The overall impression should be: “These are experienced professionals who know what they’re doing, do what they say, and can be relied upon.”

We’re open to creative interpretations. The finished card should feel distinctive through its typography, proportions, layout, and attention to detail rather than through excessive graphics or visual effects.

We’re looking for a design that would make a potential client immediately feel that they’re dealing with a capable, trustworthy, and established company.

Company Colors: Navy and Gold/Yellow (but you do not need to use these colors on the card)
Company Name: KRT Engineering Associates, Inc. (known as KRT Engineering)
Website: krtengineering.com
Company Logo: Navy & Gold (other variations attached)

```html
<!DOCTYPE html>
<html lang="en">
<head>
<meta charset="utf-8">
<title>KRT Engineering Business Card</title>
<link href="https://fonts.googleapis.com/css2?family=Lato:wght@400;700;900&family=Montserrat:wght@400;700&display=swap" rel="stylesheet">
<style>
  :root {
    --stage: #9a9a9a;
    --navy: #212b5f;
    --navy-deep: #1b2450;
    --gold: #fce14b;
    --paper: #ffffff;
    --ink: #1c1c1c;
  }
  html, body {
    margin: 0;
    padding: 0;
    width: 1200px;
    height: 1059px;
    overflow: hidden;
    background: var(--stage);
  }
  .canvas {
    position: relative;
    width: 1200px;
    height: 1059px;
  }
  .card {
    position: absolute;
    overflow: hidden;
    border-radius: 26px;
  }
  /* Front */
  .card-front {
    left: 257px;
    top: 83px;
    width: 704px;
    height: 403px;
    background: var(--paper);
  }
  .wordmark {
    position: absolute;
    margin: 0;
    font-family: "Lato", sans-serif;
    font-weight: 900;
    line-height: 1;
    letter-spacing: 1px;
  }
  .card-front .wordmark {
    left: 81px;
    top: 80px;
    font-size: 88px;
    color: var(--navy);
  }
  .identity {
    position: absolute;
    right: 29px;
    top: 62px;
    text-align: right;
    font-family: "Montserrat", sans-serif;
  }
  .identity .person-name {
    margin: 0;
    font-size: 27px;
    font-weight: 700;
    color: var(--navy);
    letter-spacing: 0.3px;
    line-height: 1.2;
  }
  .identity .person-role {
    margin: 2px 0 0;
    font-size: 19px;
    font-weight: 400;
    color: var(--ink);
    letter-spacing: 0.6px;
  }
  .accent-tab {
    position: absolute;
    right: 0;
    top: 64px;
    width: 7px;
    height: 55px;
    background: var(--navy);
  }
  .contact-list {
    position: absolute;
    left: 28px;
    top: 252px;
    margin: 0;
    padding: 0;
    list-style: none;
    font-family: "Lato", sans-serif;
    font-size: 20px;
    color: var(--ink);
  }
  .contact-list li {
    display: flex;
    align-items: center;
    height: 29px;
  }
  .contact-list svg {
    width: 24px;
    height: 22px;
    margin-right: 15px;
    fill: var(--navy);
  }
  .contact-list .web { color: #3a3a3a; }
  .address {
    position: absolute;
    left: 433px;
    top: 290px;
    margin: 0;
    font-family: "Lato", sans-serif;
    font-style: normal;
    font-size: 20px;
    line-height: 24px;
    color: var(--ink);
  }
  .front-band {
    position: absolute;
    left: 0;
    bottom: 0;
    width: 704px;
    height: 16px;
  }
  /* Back */
  .card-back {
    left: 254px;
    top: 560px;
    width: 714px;
    height: 407px;
    background: var(--navy);
  }
  .card-back .wordmark {
    left: 0;
    right: 0;
    top: 130px;
    text-align: center;
    font-size: 128px;
    color: var(--paper);
  }
  .capabilities {
    position: absolute;
    left: 0;
    right: 0;
    top: 286px;
    margin: 0;
    text-align: center;
    font-family: "Lato", sans-serif;
    font-size: 19.5px;
    line-height: 28px;
    color: var(--paper);
  }
  .capabilities .dot { color: var(--gold); }
  .back-band {
    position: absolute;
    left: 0;
    bottom: 0;
    width: 714px;
    height: 15px;
    background: var(--navy-deep);
  }
</style>
</head>
<body>
<main class="canvas">

  <section class="card card-front" aria-label="Business card front">
    <p class="wordmark">KRT</p>

    <header class="identity">
      <h1 class="person-name">DANIEL HARPER</h1>
      <p class="person-role">MANAGING DIRECTOR</p>
    </header>
    <div class="accent-tab"></div>

    <ul class="contact-list">
      <li>
        <svg viewBox="0 0 24 24" aria-hidden="true"><path d="M6.6 10.8c1.4 2.8 3.8 5.1 6.6 6.6l2.2-2.2c.3-.3.7-.4 1-.2 1.1.4 2.3.6 3.6.6.6 0 1 .4 1 1V20c0 .6-.4 1-1 1C10.6 21 3 13.4 3 4c0-.6.4-1 1-1h3.5c.6 0 1 .4 1 1 0 1.3.2 2.5.6 3.6.1.3 0 .7-.2 1z"/></svg>
        <span>044-987 654 321</span>
      </li>
      <li>
        <svg viewBox="0 0 24 20" aria-hidden="true"><path d="M1 2h22v16H1z M1 2l11 9 11-9" /><path d="M1 2h22L12 11z" fill="#fff"/></svg>
        <span>info@krtmail.com</span>
      </li>
      <li>
        <svg viewBox="0 0 24 24" aria-hidden="true"><circle cx="12" cy="12" r="10" fill="none" stroke="#212b5f" stroke-width="2"/><path d="M7 6c2 1 3 3 2 5s1 3 2 4-1 4-1 5c-4-1-7-5-7-8 1-3 2-5 4-6zM14 4c1 2 3 2 4 3s0 3 1 5 1 4 0 6c-2-1-3-3-3-5s-2-3-2-5 1-2 0-4z"/></svg>
        <span class="web">krtengineering.com</span>
      </li>
    </ul>

    <address class="address">421, Address line goes here<br>45452, Country name</address>

    <svg class="front-band" viewBox="0 0 704 16" preserveAspectRatio="none" aria-hidden="true">
      <polygon points="0,0 360,0 332,16 0,16" fill="var(--navy)"/>
      <polygon points="373,0 704,0 704,16 345,16" fill="var(--gold)"/>
    </svg>
  </section>

  <section class="card card-back" aria-label="Business card back">
    <p class="wordmark">KRT</p>
    <p class="capabilities">
      Acquisition &amp; Program Management <span class="dot">•</span> Intelligence &amp; Security Operations<br>
      <span class="dot">•</span> Cyber, IT &amp; Network Operations <span class="dot">•</span> Lifecycle Logistics &amp; Asset Readiness<br>
      <span class="dot">•</span> C5ISR Systems Engineering &amp; Sustainment
    </p>
    <div class="back-band"></div>
  </section>

</main>
</body>
</html>
```